Business card for my new company (Accounting firm)

I need a business card for my new business Brightwell Advisory and Ledger SA. Our services are accounting, tax, audit and financial management. Our customers are small companies, start-ups and new companies. The final design has to show financial security, trust and growth. Please find our logo attached to the business card. Text for the business card: Brightwell Advisory and Ledger SA Tomas Varenholt Director and Founder Certified Accountant Tel. 022 418 57 34 tv@clairevalconseil.ch www.clairevalconseil.ch Rue des Vergières 27 1201 Geneva
Target Market(s)
Our customers are small companies, start-ups and new companies.
Industry/Entity Type
Finance And Accounting
Contact Information for Business Card
Claireval Conseil et Comptes SA
Tomas Varenholt
Directeur et Fondateur
Expert-comptable diplômé
Tél. 022 418 57 34
tv@clairevalconseil.ch
www.clairevalconseil.ch
Rue des Vergières 27
1201 Genève

```html
<!DOCTYPE html>
<html lang="fr">
<head>
<meta charset="utf-8">
<title>Claireval Conseil et Comptes SA – Carte de visite</title>
<link rel="stylesheet" href="https://fonts.googleapis.com/css2?family=Montserrat:wght@500&family=Roboto:wght@400;700&display=swap">
<style>
  :root {
    --backdrop: #e4e5e7;
    --card: #ffffff;
    --ink: #333538;
    --ink-soft: #55585c;
    --blue-light: #2aa3d9;
    --blue-mid: #1e7fbf;
    --blue-deep: #17598c;
  }
  * { box-sizing: border-box; margin: 0; padding: 0; }
  html, body {
    width: 1200px; height: 726px; overflow: hidden;
    background: var(--backdrop);
  }
  .sheet {
    position: relative; width: 1200px; height: 726px;
    display: flex; align-items: center; justify-content: center; gap: 60px;
  }
  .card {
    position: relative; width: 520px; height: 310px;
    background: var(--card); overflow: hidden;
    box-shadow: 0 6px 18px rgba(0,0,0,.12);
  }

  /* Front */
  .card-front .brand {
    position: absolute; left: 0; right: 0; top: 92px;
    display: flex; align-items: center; justify-content: center; gap: 14px;
  }
  .brand-square { width: 34px; height: 34px; background: var(--blue-mid); flex: none; }
  .brand-name {
    font-family: "Montserrat", sans-serif; font-weight: 500;
    color: var(--ink); line-height: 1.05; letter-spacing: .08em;
  }
  .brand-name .main { display: block; font-size: 38px; }
  .brand-name .sub { display: block; font-size: 13px; letter-spacing: .2em; margin-top: 4px; }
  .front-stripes { position: absolute; left: 0; right: 0; bottom: 56px; }
  .front-stripes .light { height: 5px; background: var(--blue-light); }
  .front-stripes .deep { height: 4px; background: var(--blue-deep); }

  /* Back */
  .card-back .side-band {
    position: absolute; right: 0; top: 0; bottom: 0; width: 130px;
    background: var(--blue-deep);
  }
  .card-back .side-band::before {
    content: ""; position: absolute; left: -14px; top: 0; bottom: 0; width: 8px;
    background: var(--blue-light);
  }
  .card-back .brand-name { position: absolute; left: 34px; top: 34px; }
  .card-back .brand-name .main { font-size: 34px; }
  .card-back .brand-name .sub { font-size: 12px; }
  .contact {
    position: absolute; left: 34px; top: 138px;
    font-family: "Roboto", sans-serif; color: var(--ink-soft);
  }
  .person-name { font-weight: 700; font-size: 19px; color: var(--blue-deep); }
  .person-role { font-size: 11.5px; line-height: 1.35; margin-top: 3px; }
  .contact-list { list-style: none; margin-top: 12px; font-size: 13px; line-height: 1.55; color: var(--ink); }
  .contact-list li { display: flex; align-items: center; gap: 9px; }
  .contact-list svg { width: 12px; height: 12px; fill: var(--blue-deep); flex: none; }
  .address { margin-top: 4px; font-size: 12.5px; color: var(--ink); }
</style>
</head>
<body>
<main class="sheet">
  <section class="card card-front" aria-label="Recto">
    <div class="brand">
      <span class="brand-square"></span>
      <span class="brand-name">
        <span class="main">CLAIREVAL</span>
        <span class="sub">CONSEIL ET COMPTES</span>
      </span>
    </div>
    <div class="front-stripes"><div class="light"></div><div class="deep"></div></div>
  </section>

  <section class="card card-back" aria-label="Verso">
    <div class="side-band"></div>
    <span class="brand-name">
      <span class="main">CLAIREVAL</span>
      <span class="sub">CONSEIL ET COMPTES</span>
    </span>
    <div class="contact">
      <p class="person-name">Tomas Varenholt</p>
      <p class="person-role">Directeur et Fondateur<br>Expert-comptable diplômé</p>
      <ul class="contact-list">
        <li><svg viewBox="0 0 12 12"><path d="M2 1h3l1 3-2 1a7 7 0 0 0 3 3l1-2 3 1v3c0 .6-.4 1-1 1A10 10 0 0 1 1 2c0-.6.4-1 1-1z"/></svg>022 418 57 34</li>
        <li><svg viewBox="0 0 12 12"><path d="M0 2h12v8H0zM1 3v.4l5 3.3 5-3.3V3z" fill-rule="evenodd"/></svg>tv@clairevalconseil.ch</li>
        <li><svg viewBox="0 0 12 12"><path d="M6 0a6 6 0 1 0 0 12A6 6 0 0 0 6 0zm0 1.2c.7.8 1.2 2.3 1.3 4.2H4.7C4.8 3.5 5.3 2 6 1.2zM1.2 6.6h2.4c.1 1.5.4 2.8.9 3.7a4.8 4.8 0 0 1-3.3-3.7zm0-1.2a4.8 4.8 0 0 1 3.3-3.7c-.5.9-.8 2.2-.9 3.7zm3.5 1.2h2.6c-.1 1.9-.6 3.4-1.3 4.2-.7-.8-1.2-2.3-1.3-4.2zm3.7 0h2.4a4.8 4.8 0 0 1-3.3 3.7c.5-.9.8-2.2.9-3.7zm0-1.2c-.1-1.5-.4-2.8-.9-3.7a4.8 4.8 0 0 1 3.3 3.7z"/></svg>www.clairevalconseil.ch</li>
      </ul>
      <p class="address">Rue des Vergières 27 1201 Genève</p>
    </div>
  </section>
</main>
</body>
</html>
```